GTP biz card

We need a business card design for our new company based in Los Angeles called "Gold Tide Pictures". We develop film and television projects. We work with investors, financiers, film production companies, film distribution and sales companies as well as studios. We would like to incorporate our logo (see attached) on a two-sided card. We need to include: name and title, address, phone, email and company website.

Target Market(s)

Business, financial and studio clients

Industry/Entity Type

Business

Contact Information for Business Card

Two-sided. We are thinking of the logo on one side and the information on the back. Please feel free to be creative! Thanks.

Requirements
Must have
• Please include the following text information, excluding the "CAPS CATEGORY:" and please allow the ability for us to change the name, title and email address for each company employee):
• NAME & TITLE:
• Neil Parker
• Managing Partner
• COMPANY NAME:
• GOLD TIDE PICTURES (please use existing logo)
• COMPANY ADDRESS:
• KTW Studio Park
• 2250 Halverd Street
• Harbor Wing, 4th Floor
• Manhattan Beach, CA 90412
• COMPANY PHONE NUMBER:
• 310-555-0148
• COMPANY WEBSITE ADDRESS:
• www.goldtidepicturesgroup.example
• EMAIL ADDRESS: (only one per card)
• peter@goldtidepicturesgroup.example
• bingo@goldtidepicturesgroup.example
• neil@goldtidepicturesgroup.example

```html
<!DOCTYPE html>
<html lang="en">
<head>
<meta charset="utf-8">
<title>Gold Tide Pictures – Business Card</title>
<link rel="stylesheet" href="https://fonts.googleapis.com/css2?family=Exo+2:wght@400;600&display=swap">
<style>
  :root {
    --backdrop: #ebebeb;
    --card-dark: #231f20;
    --card-grey: #6b7078;
    --accent-blue: #1e7fcf;
    --accent-light: #5aa3e0;
    --paper: #ffffff;
    --ink: #444444;
    --ink-dark: #222222;
    --mark-fill: #0f4f68;
    --brand-blue: #29a8e0;
  }
  html, body {
    margin: 0;
    padding: 0;
    width: 1200px;
    height: 1000px;
    overflow: hidden;
    background: var(--backdrop);
    font-family: "Exo 2", sans-serif;
  }
  .canvas { position: relative; width: 1200px; height: 1000px; }
  .card {
    position: absolute;
    left: 316px;
    width: 548px;
    height: 323px;
    box-shadow: 3px 4px 4px rgba(0,0,0,0.45);
    overflow: hidden;
  }
  .card--info {
    top: 147px;
    background: linear-gradient(to right,
      var(--card-dark) 0%,
      var(--card-dark) 19%,
      var(--card-grey) 39%,
      var(--accent-blue) 41.8%,
      var(--accent-light) 43.8%,
      var(--paper) 51.3%,
      var(--paper) 100%);
  }
  .card--brand { top: 532px; background: var(--card-dark); }

  .brand-lockup {
    position: absolute;
    display: flex;
    flex-direction: column;
    align-items: center;
  }
  .brand-mark { display: block; }
  .brand-name {
    color: var(--brand-blue);
    font-weight: 600;
    white-space: nowrap;
    letter-spacing: 0.06em;
  }
  .card--info .brand-lockup { left: 19px; top: 124px; width: 100px; }
  .card--info .brand-name { font-size: 10px; margin-top: 6px; }
  .card--brand .brand-lockup { left: 0; right: 0; top: 58px; }
  .card--brand .brand-name { font-size: 27px; margin-top: 12px; }

  .contact {
    position: absolute;
    right: 33px;
    text-align: right;
    color: var(--ink);
    font-size: 16px;
    line-height: 20px;
  }
  .contact p { margin: 0; }
  .contact strong { font-weight: 600; }
  .contact--person { top: 47px; }
  .contact--address { top: 143px; }
  .contact--web { top: 264px; color: var(--ink-dark); }
</style>
</head>
<body>
<main class="canvas">
  <section class="card card--info" aria-label="Business card, contact side">
    <div class="brand-lockup">
      <svg class="brand-mark" width="60" height="60" viewBox="0 0 60 60" aria-hidden="true">
        <circle cx="30" cy="30" r="29" fill="var(--mark-fill)"/>
      </svg>
      <span class="brand-name">GOLD TIDE PICTURES</span>
    </div>

    <div class="contact contact--person">
      <p><strong>Neil Parker</strong></p>
      <p><strong>Director</strong></p>
      <p>neil@goldtidepicturesgroup.example</p>
    </div>

    <div class="contact contact--address">
      <p><strong>KTW Studio Park</strong></p>
      <p>2250 Halverd Street</p>
      <p>Harbor Wing, 4th Floor</p>
      <p>Manhattan Beach, CA 90412</p>
      <p>Phone: 310-555-0148</p>
    </div>

    <div class="contact contact--web">
      <p>www.goldtidepicturesgroup.example</p>
    </div>
  </section>

  <section class="card card--brand" aria-label="Business card, brand side">
    <div class="brand-lockup">
      <svg class="brand-mark" width="134" height="134" viewBox="0 0 134 134" aria-hidden="true">
        <circle cx="67" cy="67" r="66" fill="var(--mark-fill)"/>
      </svg>
      <span class="brand-name">GOLD TIDE PICTURES</span>
    </div>
  </section>
</main>
</body>
</html>
```